Chai Tea Company needs a Tea Packaging Box Design

Tea Packaging
Dimensions of the Tea Packaging Box: Height 13 cm; Width 8.5 cm; Depth 7 cm
Individual Teabag Packet/ Sachet: Width 6.5 cm; Length 8.25 cm
We are looking for a new tea packaging design, for our tea business. The material of the box is cardboard. We are also looking for a design that will be on each individual tea bag sachet/packet that goes into the box. This design will be very similar to what you design for the tea packaging box.
Product Info:
Our tea company is called “Velmora Brew”. We sell two types of Chai Tea, once called “Velmora Gold” and one called “Velmora Meadow”. The Velmora Gold has caffeine, while the Velmora Meadow is Naturally Caffeine Free. The Velmora Gold has a black tea base, while the Velmora Meadow has a Rooibos tea base. We will need two tea packaging designs, one for each Chai Tea flavour. The designs for both the teas can be similar, but make sure that you can easily distinguish one from the other (example: make them have different colours or pictures). Both the chai teas, come from the same product line.
Tea Packaging Design:
We are looking for high end tea packaging. We produce high quality teas, and we would like to portray this in our tea packaging. Our teas are made with no artificial flavourings, natural flavourings, or preservatives, so we would also like a natural, organic, high quality look to our tea packaging. Our current logo is a llama. It would be great if you could make the current logo more polished and well made. If you feel that the llama is not well suited or you would like to design the llama differently, we are open to your creative ideas.
General Basic Info:
Keep in mind, we will have both English and French writing on the tea packaging. You do not need to worry about the French writing (we will do the translation), just make sure there is room for it. However, if you feel that you are capable and knowledgeable of incorporating both French and English language into the tea packaging that would be of great help and value.
Back of the Box:
- Will have ingredients and brewing instructions. Basic brewing instructions are: “Add hot water to teabag. Steep for 5-7 minutes, depending on strength preferred. Add milk and your choice of sweetener. Enjoy! See inside panel of box for more detailed instructions”. (The basic brewing instructions, can further be polished or written in a more creative or professional manner).
Front of the Box:
- Will have company name, type of tea, little description of the tea
- 18 teabags
- 54 g (1.9 OZ)
- Should state that this is a product of Alberta, Canada.
Side of the Box:
Any creative wording, slogan, or description about the tea, or whatever you feel would be good on the side of the box.
On the inside flap of the side of the box, there will be detailed instructions on how to brew the tea. These will be different from the simplified brewing instructions on the back of the box. I have attached the advanced brewing instructions as a file. These instructions can further be simplified or reduced to make it easier and cleaner for the consumers to read.
Individual Tea Sachets/ Packets
- These will have a matching look and design of the tea box packaging, except on a smaller scale. Each individual sachet will have the company name, type of tea, little description of the tea in the front of the sachet, while the back will contain the ingredients, and basic brewing instructions.
I have attached a few files, with the dimensions, ingredients, detailed brewing directions, and current logo of the business.
If you have any questions, about the design or packaging please let me know. The winning designer will be required to do a few additional tweaks to finalize the product. Thank you for your time and happy designing!

```html
<!DOCTYPE html>
<html lang="en">
<head>
<meta charset="utf-8">
<title>Velmora Meadow – Chai Tea Box Front</title>
<link rel="stylesheet" href="https://fonts.googleapis.com/css2?family=Marcellus+SC&family=Yesteryear&display=swap">
<style>
  :root {
    --maroon: #4a0709;
    --paper: #ececec;
    --gold: #9c8656;
    --rule-gold: #a68f5e;
    --berry: #a0393d;
    --berry-dark: #8f2f33;
    --llama-light: #d7918c;
    --llama-dark: #983a3e;
    --dash: #222;
  }
  * { margin: 0; padding: 0; box-sizing: border-box; }
  html, body { width: 1200px; height: 1000px; overflow: hidden; }
  body { background: var(--maroon); position: relative; font-family: "Marcellus SC", serif; }

  .front-panel {
    position: absolute; left: 211px; top: 0; width: 788px; height: 1000px;
    background: linear-gradient(180deg, #efefef, var(--paper));
    text-align: center;
  }
  .perforation {
    position: absolute; left: 0; top: 0; width: 100%; height: 3px;
    background: repeating-linear-gradient(90deg, transparent 0 38px, var(--dash) 38px 68px, transparent 68px 100px);
  }
  .tea-type {
    position: absolute; left: 0; width: 100%; top: 50px;
    color: var(--gold); font-size: 31px; letter-spacing: 1px;
  }
  .tea-type .divider {
    display: inline-block; width: 16px; height: 16px; background: var(--berry);
    margin: 0 34px; vertical-align: 2px;
  }
  .caffeine-note {
    position: absolute; left: 0; width: 100%; top: 94px;
    color: var(--gold); font-size: 22px; word-spacing: 2px;
  }
  .caffeine-note span + span { margin-left: 56px; }

  .product-name {
    position: absolute; left: 0; width: 100%; top: 150px;
    font-family: "Yesteryear", cursive; font-weight: 400;
    font-size: 100px; line-height: 1.1; color: var(--berry);
    text-shadow: 3px 4px 0 #fff, 5px 6px 0 var(--berry);
  }

  .description {
    position: absolute; left: 60px; width: 668px;
    color: var(--berry); font-size: 21px; line-height: 21px;
  }
  .description.en { top: 316px; }
  .description.fr { top: 400px; font-size: 20px; color: var(--berry-dark); }
  .gold-rule {
    position: absolute; left: 76px; top: 387px; width: 639px; height: 4px;
    background: var(--rule-gold);
  }

  .mascot {
    position: absolute; left: 134px; top: 510px; width: 526px; height: 490px;
    border-radius: 46% 54% 0 0 / 30% 40% 0 0;
    background: linear-gradient(180deg, var(--llama-light) 0%, var(--llama-light) 40%, var(--llama-dark) 75%);
    opacity: 0.9;
  }
</style>
</head>
<body>
  <main class="front-panel">
    <div class="perforation"></div>
    <p class="tea-type">Chai Tea<span class="divider"></span>Thé chai</p>
    <p class="caffeine-note"><span>caffeine free</span><span>sans caféine</span></p>
    <h1 class="product-name">Velmora Meadow</h1>
    <p class="description en">A rich blend of South African<br>Rooibos Tea, Cardamon, Fennel,<br>Cloves, Ginger and Cinnamon</p>
    <div class="gold-rule"></div>
    <p class="description fr">Un riche mélange du thé rooibos d'Afrique<br>du Sud, la cardamome, le fenouil, clous de<br>girofle, le gingembre et la cannelle</p>
    <div class="mascot" role="img" aria-label="Rose-toned llama illustration standing in profile"></div>
  </main>
</body>
</html>
```